Thornvale Group needs a business card design

We need a new business card design using the logo recently selected in a logo competition on Pixel Bazaar. Our business is a consultancy specializing in aviation and energy and the winning business card design will promote an image of precision and professionalism with creativity.

Please use the logo with the name on the front of the card and use a complementary font. Make the back white with either the light grey or dark grey logo.

Target Market(s)

Senior finance and legal leaders at aviation and energy companies

Industry/Entity Type

Management Consulting

Contact Information for Business Card

Peter Castrell
President
Thornvale Group

www.thornvalegroup.example

(555) 204-6391
pc@thornvalegroup.example

Requirements
Must have
• Professional font that goes well with the logo font

```html
<!DOCTYPE html>
<html lang="en">
<head>
<meta charset="utf-8">
<title>Thornvale Group – Business Card</title>
<link rel="stylesheet" href="https://fonts.googleapis.com/css2?family=Open+Sans:wght@400;600;700&family=Roboto+Condensed:wght@400;700&display=swap">
<style>
  :root {
    --navy: #0d3f6e;
    --ink-grey: #555a60;
    --mark-grey: #636466;
    --card: #ffffff;
    --backdrop: #e9e6e3;
  }
  * { margin: 0; padding: 0; box-sizing: border-box; }
  html, body { width: 1200px; height: 900px; overflow: hidden; }
  body {
    position: relative;
    background: var(--backdrop);
    font-family: "Open Sans", Arial, sans-serif;
  }
  .card {
    position: absolute;
    background: var(--card);
    box-shadow: 0 2px 8px rgba(0,0,0,0.12);
    overflow: hidden;
  }
  .card--front { left: 238px; top: 62px; width: 555px; height: 342px; }
  .card--back  { left: 457px; top: 519px; width: 560px; height: 342px; }

  .corner { position: absolute; display: block; }
  .corner--top-right { right: 0; top: 0; width: 114px; height: 89px; }
  .corner--bottom-left { left: 0; bottom: 0; width: 108px; height: 92px; }
  .corner path { fill: var(--navy); }

  .brand {
    position: absolute;
    left: 42px; top: 132px;
    display: flex; align-items: center; gap: 10px;
    color: var(--navy);
    font-size: 24px; font-weight: 400;
    letter-spacing: 1px;
    white-space: nowrap;
  }
  .brand__dot { width: 14px; height: 14px; background: var(--navy); }

  .contact { position: absolute; left: 298px; top: 90px; }
  .contact__name { color: var(--navy); font-size: 18px; font-weight: 700; line-height: 1.2; }
  .contact__role { color: var(--ink-grey); font-size: 14px; line-height: 1.3; }
  .contact__lines { margin-top: 26px; list-style: none; }
  .contact__line {
    display: flex; align-items: center; gap: 8px;
    color: var(--ink-grey); font-size: 14px; line-height: 20px;
  }
  .contact__icon { width: 12px; height: 12px; fill: var(--navy); }

  .tagline {
    position: absolute; left: 0; right: 0; top: 256px;
    text-align: center;
    font-family: "Roboto Condensed", Arial, sans-serif;
    padding-left: 10px;
  }
  .tagline__service { color: var(--navy); font-size: 16px; font-weight: 700; line-height: 1.4; }
  .tagline__sectors { color: var(--ink-grey); font-size: 16px; font-weight: 400; line-height: 1.5; }

  .back-brand {
    position: absolute; inset: 0;
    display: flex; align-items: center; justify-content: center; gap: 14px;
    color: var(--mark-grey);
    font-size: 34px; font-weight: 400; letter-spacing: 1px;
  }
  .back-brand__dot { width: 20px; height: 20px; background: var(--mark-grey); }
</style>
</head>
<body>
  <section class="card card--front" aria-label="Business card front">
    <svg class="corner corner--top-right" viewBox="0 0 114 89" aria-hidden="true"><path d="M0 0H114V89Z"/></svg>
    <svg class="corner corner--bottom-left" viewBox="0 0 108 92" aria-hidden="true"><path d="M0 0L108 92H0Z"/></svg>

    <div class="brand"><span class="brand__dot"></span>Thornvale Group</div>

    <div class="contact">
      <p class="contact__name">Peter Castrell</p>
      <p class="contact__role">President</p>
      <ul class="contact__lines">
        <li class="contact__line">
          <svg class="contact__icon" viewBox="0 0 24 24" aria-hidden="true"><path d="M6.6 10.8a15.1 15.1 0 0 0 6.6 6.6l2.2-2.2a1 1 0 0 1 1-.25 11.4 11.4 0 0 0 3.6.57 1 1 0 0 1 1 1V20a1 1 0 0 1-1 1A17 17 0 0 1 3 4a1 1 0 0 1 1-1h3.5a1 1 0 0 1 1 1c0 1.25.2 2.45.57 3.57a1 1 0 0 1-.25 1Z"/></svg>
          (555) 204-6391
        </li>
        <li class="contact__line">
          <svg class="contact__icon" viewBox="0 0 24 24" aria-hidden="true"><path d="M2 5h20v14H2Zm2 2v.5l8 5 8-5V7l-8 5Z"/></svg>
          pc@thornvalegroup.example
        </li>
      </ul>
    </div>

    <div class="tagline">
      <p class="tagline__service">Finance and Strategy Consulting</p>
      <p class="tagline__sectors">Aviation - Manufacturing - Energy</p>
    </div>
  </section>

  <section class="card card--back" aria-label="Business card back">
    <div class="back-brand"><span class="back-brand__dot"></span>Thornvale Group</div>
  </section>
</body>
</html>
```